Lifestyle Coaching comp needs wordpress design. We focus on strong mindsets, fitness and nutrition

BrenVigor Lifestyle Coaching needs a wordpress site. Our tagline for now (may change) is Mindset Mastery.Fitness Badassery. Sustainable Nutrition
Our logo is below. Would like to see some complimentary colors to liven it up. Clients need to come to site and get immediate professional, but fun feel. They need to have the impression that we are the last destination in their journey to wellness. Blogging, workout videos, pictures

Target Market(s)

Mostly women ages 20+

Industry/Entity Type

Nutrition

Colors
33a6d7
86cae7
ceeaf6
cfdeed
5c5c5c
cbcbcb
474747

Requirements
Must have
• A strong, badass feel :) While not being intimidating
Nice to have
• Fun fonts. Love the font in my logo
Should not have
• Pics, logos of flowers, heads, fruit.

```html
<!DOCTYPE html>
<html lang="en">
<head>
<meta charset="utf-8">
<title>BrenVigor Lifestyle Coaching</title>
<link rel="stylesheet" href="https://fonts.googleapis.com/css2?family=Open+Sans:wght@400;600;700;800&display=swap">
<style>
:root{
  --blue:#33a6d7;
  --blue-mid:#86cae7;
  --blue-light:#ceeaf6;
  --blue-grey:#cfdeed;
  --text:#5c5c5c;
  --text-dark:#474747;
  --line:#cbcbcb;
  --green:#9bd26a;
  --panel:#f1f1f1;
  --footer:#2a2a2a;
  --white:#ffffff;
}
*{margin:0;padding:0;box-sizing:border-box}
html,body{width:1200px;height:2636px;overflow:hidden}
body{position:relative;background:var(--white);font-family:"Open Sans",Arial,sans-serif;color:var(--text)}
.abs{position:absolute}

/* hero */
.hero{left:0;top:0;width:1200px;height:700px;background:linear-gradient(180deg,#4fa9dc 0%,#8fcbee 38%,#cde8f6 52%,#3e8fc0 60%,#6fb0cf 66%,#7fb04a 74%,#5f9a32 100%)}
.nav-bar{left:120px;top:44px;width:980px;height:90px;background:var(--white);box-shadow:0 3px 10px rgba(0,0,0,.15);display:flex;align-items:center;padding:0 30px}
.brand{display:flex;align-items:center;gap:12px;font-size:22px;font-weight:800;color:var(--blue);letter-spacing:1px}
.brand-dot{width:28px;height:28px;border-radius:50%;background:var(--blue)}
.nav-links{margin-left:auto;display:flex;height:100%}
.nav-links a{display:flex;align-items:center;padding:0 22px;font-size:13px;font-weight:600;color:var(--text-dark);text-decoration:none;letter-spacing:.5px}
.nav-links a.active{background:var(--blue);color:var(--white)}
.hero-title{left:120px;top:262px;font-size:46px;font-weight:800;color:var(--green);letter-spacing:1px}
.hero-sub{left:120px;top:334px;font-size:20px;line-height:30px;color:var(--white);font-weight:600}
.btn{display:inline-block;background:var(--blue);color:var(--white);font-size:13px;font-weight:700;letter-spacing:.5px;border-radius:22px;text-align:center}
.hero-btn{left:120px;top:428px;width:130px;height:42px;line-height:42px;border-radius:4px}
.hero-shadow{left:60px;top:700px;width:1080px;height:26px;background:radial-gradient(ellipse at top,rgba(0,0,0,.22),rgba(0,0,0,0) 70%)}

/* section heads */
.section-title{left:0;width:1200px;text-align:center;font-size:30px;font-weight:800;color:var(--text-dark);letter-spacing:1px}
.section-title span{color:var(--blue)}
.section-sub{left:0;width:1200px;text-align:center;font-size:15px;color:#9a9a9a}

/* features */
.feature{width:260px;text-align:center}
.feature-icon{width:92px;height:92px;border-radius:50%;background:var(--blue);margin:0 auto 22px;display:flex;align-items:center;justify-content:center}
.feature h3{font-size:16px;font-weight:800;color:var(--text-dark);margin-bottom:12px}
.feature p{font-size:12px;line-height:19px;color:var(--text)}

/* photos */
.photo{top:1228px;width:245px;height:190px}

/* videos */
.videos{left:0;top:1470px;width:1200px;height:360px;background:var(--panel)}
.video-media{left:0;top:1470px;width:560px;height:360px;background:linear-gradient(120deg,#d8e6ef 0%,#a9c9dd 40%,#e2a7c5 70%,#cfe0ea 100%)}
.play{left:250px;top:1620px;width:64px;height:64px;border-radius:50%;background:rgba(255,255,255,.85)}
.video-copy{left:600px;top:1520px;width:520px}
.video-copy h2{font-size:28px;font-weight:800;color:var(--text-dark);margin-bottom:10px}
.video-copy h2 span{color:var(--blue)}
.video-copy .lead{font-size:13px;line-height:20px;font-weight:700;color:var(--text-dark);margin-bottom:22px}
.video-copy p{font-size:12px;line-height:21px;margin-bottom:18px}

/* blog */
.card{top:1960px;width:310px;height:440px;background:var(--white);box-shadow:0 10px 14px -10px rgba(0,0,0,.35)}
.card-media{width:310px;height:205px}
.card-body{padding:22px 18px 0}
.card h4{font-size:13px;font-weight:800;color:var(--text-dark);margin-bottom:12px}
.meta{display:flex;gap:16px;font-size:11px;color:#999;margin-bottom:14px}
.meta i{display:inline-block;width:9px;height:9px;background:var(--line);margin-right:5px;vertical-align:-1px}
.card p{font-size:12px;line-height:19px}
.card .btn{position:absolute;left:95px;bottom:18px;width:120px;height:38px;line-height:38px}

/* footer */
.footer{left:0;top:2460px;width:1200px;height:176px;background:var(--footer)}
.social{top:2484px;left:0;width:1200px;display:flex;justify-content:center;gap:16px}
.social span{width:34px;height:34px;border-radius:50%;background:#4a4a4a}
.foot-nav{top:2544px;left:0;width:1200px;display:flex;justify-content:center;gap:36px;font-size:12px;font-weight:600;color:var(--white);letter-spacing:.5px}
.copy{top:2584px;left:0;width:1200px;text-align:center;font-size:12px;color:#9a9a9a}
</style>
</head>
<body>

<section class="hero abs" role="img" aria-label="Woman stretching in a yoga pose on grass by the sea under a blue sky"></section>
<header class="nav-bar abs">
  <div class="brand"><span class="brand-dot"></span>BRENVIGOR</div>
  <nav class="nav-links">
    <a class="active">HOME</a><a>ABOUT US</a><a>SERVICES</a><a>FEATURES</a><a>BLOG</a><a>GALLERY</a><a>CONTACT US</a>
  </nav>
</header>
<h1 class="hero-title abs">LIFESTYLE COACHING</h1>
<p class="hero-sub abs">Mindset Mastery.Fitness Badassery.<br>Sustainable Nutrition</p>
<span class="btn hero-btn abs">READ MORE</span>
<div class="hero-shadow abs"></div>

<h2 class="section-title abs" style="top:766px">WELCOME TO <span>OUR COMPANY</span></h2>
<p class="section-sub abs" style="top:816px">Clear goals, steady habits and real support for every step forward</p>

<div class="feature abs" style="left:150px;top:868px">
  <div class="feature-icon"><svg width="44" height="44" viewBox="0 0 44 44"><circle cx="22" cy="14" r="7" fill="#fff"/><path d="M8 38c2-10 26-10 28 0z" fill="#fff"/></svg></div>
  <h3>STRONG MINDSETS</h3>
  <p>Build the mental habits that keep you moving when motivation fades, one small win at a time.</p>
</div>
<div class="feature abs" style="left:470px;top:868px">
  <div class="feature-icon"><svg width="48" height="48" viewBox="0 0 48 48"><rect x="6" y="18" width="6" height="12" fill="#fff"/><rect x="36" y="18" width="6" height="12" fill="#fff"/><rect x="12" y="14" width="5" height="20" fill="#fff"/><rect x="31" y="14" width="5" height="20" fill="#fff"/><rect x="17" y="22" width="14" height="4" fill="#fff"/></svg></div>
  <h3>FITNESS</h3>
  <p>Workouts shaped around your life, your level and your goals, so strength feels fun again.</p>
</div>
<div class="feature abs" style="left:790px;top:868px">
  <div class="feature-icon"><svg width="44" height="44" viewBox="0 0 44 44"><path d="M6 20h32a16 16 0 0 1-32 0z" fill="#fff"/><rect x="20" y="8" width="4" height="10" fill="#fff"/></svg></div>
  <h3>NUTRITION</h3>
  <p>Simple, lasting eating habits with no crash diets, just real food and balanced daily choices.</p>
</div>

<h2 class="section-title abs" style="top:1146px">RECENT <span>PHOTOS</span></h2>
<p class="section-sub abs" style="top:1194px">Moments from our classes, retreats and outdoor training sessions</p>
<div class="photo abs" style="left:80px;background:linear-gradient(160deg,#b9d7ea,#e59bc2 55%,#8a8f86)" role="img" aria-label="Two women jogging on an outdoor track"></div>
<div class="photo abs" style="left:345px;background:linear-gradient(160deg,#7d7f84,#c9b3a1 55%,#3e3f43)" role="img" aria-label="Woman doing a plank exercise in a gym"></div>
<div class="photo abs" style="left:610px;background:linear-gradient(160deg,#d6e6b8,#f0a0c4 50%,#89b45a)" role="img" aria-label="Woman stretching on a mat outdoors"></div>
<div class="photo abs" style="left:875px;background:linear-gradient(160deg,#f1c48a,#e99a5a 50%,#6b8f57)" role="img" aria-label="Woman in a yoga pose at sunset"></div>

<section class="videos abs"></section>
<div class="video-media abs" role="img" aria-label="Group fitness class exercising with exercise balls"></div>
<svg class="play abs" viewBox="0 0 64 64"><circle cx="32" cy="32" r="32" fill="rgba(255,255,255,.85)"/><path d="M26 20l18 12-18 12z" fill="#33a6d7"/></svg>
<div class="video-copy abs">
  <h2>WORKOUT <span>VIDEOS</span></h2>
  <p class="lead">Get a quick look at our latest home routines, stretches and full body sessions for any level</p>
  <p>Each video is short, clear and easy to follow, so you can train at home, at the park or on the road. Pick a session, press play and move with us.</p>
  <p>New sessions arrive every week covering strength, mobility, cardio and recovery. Save your favourites and build a routine that fits your schedule and keeps you coming back.</p>
</div>

<h2 class="section-title abs" style="top:1866px">LATEST <span>BLOG</span></h2>
<p class="section-sub abs" style="top:1914px">Fresh stories, tips and real wins from our coaching community</p>

<article class="card abs" style="left:100px">
  <div class="card-media" style="background:linear-gradient(180deg,#e8f1f8,#c9dcea)" role="img" aria-label="Woman meditating in white clothing"></div>
  <div class="card-body">
    <h4>NEQUE PORRO QUISQUAM EST</h4>
    <div class="meta"><span><i></i>Jun 12</span><span><i></i>Admin</span><span><i></i>4 Likes</span></div>
    <p>Quick tips on rest days, hydration and mindset to help you stay on track all week long.</p>
  </div>
  <span class="btn">READ MORE</span>
</article>
<article class="card abs" style="left:445px">
  <div class="card-media" style="background:linear-gradient(180deg,#8b8c90,#4b4c50)" role="img" aria-label="Woman stretching on the floor of a gym"></div>
  <div class="card-body">
    <h4>NEQUE PORRO QUISQUAM EST</h4>
    <div class="meta"><span><i></i>Jun 09</span><span><i></i>Admin</span><span><i></i>7 Likes</span></div>
    <p>Why short daily stretches matter and how to add them to a busy morning routine easily.</p>
  </div>
  <span class="btn">READ MORE</span>
</article>
<article class="card abs" style="left:790px">
  <div class="card-media" style="background:linear-gradient(180deg,#9fb7cf,#d99ab5 60%,#7c6a8e)" role="img" aria-label="Group class doing a side stretch together"></div>
  <div class="card-body">
    <h4>NEQUE PORRO QUISQUAM EST</h4>
    <div class="meta"><span><i></i>Jun 02</span><span><i></i>Admin</span><span><i></i>5 Likes</span></div>
    <p>A simple guide to group classes, what to bring and how to get the most out of them.</p>
  </div>
  <span class="btn">READ MORE</span>
</article>

<footer class="footer abs"></footer>
<div class="social abs"><span></span><span></span><span></span><span></span></div>
<nav class="foot-nav abs"><span>HOME</span><span>ABOUT US</span><span>SERVICES</span><span>FEATURES</span><span>BLOG</span><span>GALLERY</span><span>CONTACT US</span></nav>
<p class="copy abs">© Copy Rights 2016 | BrenVigor Lifestyle Coaching | All Rights Reserved</p>

</body>
</html>
```